Billboard for Real Estate Agent

I need a signage design for my billboard that is going up end of December.

-I target the higher end waterfront properties ($1,000,000 +) in Marlin Shoals, QLD, Australia so it needs to be sleek, funky yet sophisticated and professional and needs to have my photo- or if you have an idea with someone else's photo, then I can have one taken that's the same.

-The purpose is to target those who are thinking about selling/buying property.
We want people to remember the ad, so it's top of mind.

-The billboard is on the side of the road, and will be lit up at night and I'll have it for 13 months. Needs to be noticeable from the road, but nothing tacky and too loud.

Needs to have my name, Maren Thistlewood and my contact number and business logo (attached).

Maren Thistlewood
0493 615 207

Target Market(s)

Wealthy demographic 25-65 years old.

Industry/Entity Type

Business

Requirements
Must have
• My name, phone number and HOMVIA logo attached.

Pylo Guidelines:
http://www.pylo-example.com.au/our-resources/artwork-guidelines/

Heading: Don't be a Dinosaur
Subline: Think Differently

Use one of the photos.
Nice to have
• -Quirky, different and captivating (i've attached some wacky billboard ideas)

```html
<!DOCTYPE html>
<html lang="en">
<head>
<meta charset="utf-8">
<title>Maren Thistlewood – Billboard</title>
<link rel="stylesheet" href="https://fonts.googleapis.com/css2?family=Arimo:wght@700&display=swap">
<style>
  :root {
    --canvas: #ffffff;
    --board: #4a4a4a;
    --board-dark: #3f3f3f;
    --ink-white: #ffffff;
    --ink-black: #111111;
    --cyan: #1fc4dc;
    --band: #19a9bd;
    --yellow: #ffee1a;
    --navy: #1d2a57;
    --faint: rgba(0, 0, 0, 0.16);
  }
  * { margin: 0; padding: 0; box-sizing: border-box; }
  html, body {
    width: 1162px;
    height: 1200px;
    overflow: hidden;
    background: var(--canvas);
  }
  .billboard {
    position: absolute;
    left: 22px;
    top: 342px;
    width: 1118px;
    height: 516px;
    background: var(--board);
    overflow: hidden;
    font-family: "Arimo", Arial, sans-serif;
    font-weight: 700;
  }
  .brand-watermark {
    position: absolute;
    left: -150px;
    top: -40px;
    width: 430px;
    height: 430px;
    border-radius: 50%;
    background: var(--faint);
  }
  .brand-watermark-name {
    position: absolute;
    left: 6px;
    top: 40px;
    font-size: 64px;
    color: var(--faint);
    letter-spacing: 1px;
  }
  .headline {
    position: absolute;
    left: 24px;
    top: 96px;
    width: 812px;
    text-align: right;
    font-size: 66px;
    line-height: 1;
    color: var(--ink-white);
    -webkit-text-stroke: 6px var(--ink-black);
    paint-order: stroke fill;
    white-space: nowrap;
  }
  .subline {
    position: absolute;
    left: 24px;
    top: 170px;
    width: 812px;
    text-align: right;
    font-size: 42px;
    line-height: 1;
    color: var(--cyan);
    white-space: nowrap;
  }
  .agent-name {
    position: absolute;
    left: 187px;
    top: 240px;
    width: 600px;
    text-align: center;
    color: var(--ink-white);
    -webkit-text-stroke: 6px var(--ink-black);
    paint-order: stroke fill;
    line-height: 1;
    white-space: nowrap;
  }
  .agent-first { display: block; font-size: 72px; letter-spacing: 2px; }
  .agent-last { display: block; font-size: 54px; margin-top: 10px; }
  .contact-band {
    position: absolute;
    left: 0;
    top: 400px;
    width: 100%;
    height: 84px;
    background: var(--band);
  }
  .brand-name {
    position: absolute;
    left: 70px;
    top: 24px;
    font-size: 34px;
    color: var(--navy);
    letter-spacing: 1px;
  }
  .phone {
    position: absolute;
    left: 284px;
    top: 10px;
    display: flex;
    align-items: center;
    gap: 22px;
  }
  .phone-icon { width: 88px; height: 62px; }
  .phone-number {
    font-size: 72px;
    line-height: 1;
    color: var(--yellow);
    -webkit-text-stroke: 5px var(--ink-black);
    paint-order: stroke fill;
    letter-spacing: 1px;
    white-space: nowrap;
  }
  .agent-photo-glow {
    position: absolute;
    left: 820px;
    top: 0;
    width: 298px;
    height: 516px;
    background: radial-gradient(ellipse at 55% 50%, #cfcfcf 0%, #a8a8a8 45%, rgba(74, 74, 74, 0) 75%);
  }
  .agent-photo {
    position: absolute;
    left: 850px;
    top: 30px;
    width: 260px;
    height: 486px;
    border-radius: 40px 40px 0 0;
    background: linear-gradient(180deg, #4e3a30 0%, #b98d78 38%, #d9b09a 52%, #2aa9ad 72%, #1e8f97 100%);
  }
</style>
</head>
<body>
  <main class="billboard">
    <div class="brand-watermark" aria-hidden="true"></div>
    <div class="brand-watermark-name" aria-hidden="true">HOMVIA</div>

    <h1 class="headline">DON'T BE A DINOSAUR</h1>
    <p class="subline">...DO THINGS DIFFERENTLY</p>

    <h2 class="agent-name">
      <span class="agent-first">MAREN</span>
      <span class="agent-last">THISTLEWOOD</span>
    </h2>

    <div class="contact-band">
      <span class="brand-name">HOMVIA</span>
      <div class="phone">
        <svg class="phone-icon" viewBox="0 0 88 62" aria-hidden="true">
          <path d="M6 20 Q6 6 44 6 Q82 6 82 20 L82 26 L62 26 L62 18 L26 18 L26 26 L6 26 Z"
                fill="#ffee1a" stroke="#111" stroke-width="4" stroke-linejoin="round"/>
          <path d="M22 28 L66 28 L78 56 L10 56 Z"
                fill="#ffee1a" stroke="#111" stroke-width="4" stroke-linejoin="round"/>
          <circle cx="44" cy="42" r="9" fill="none" stroke="#111" stroke-width="4"/>
        </svg>
        <span class="phone-number">0493.615.207</span>
      </div>
    </div>

    <div class="agent-photo-glow" aria-hidden="true"></div>
    <div class="agent-photo" role="img" aria-label="Portrait photo of the agent, smiling, wearing a teal top"></div>
  </main>
</body>
</html>
```